"Velmora Crest" sexual performance enhancement pill bottle label needed.

This should be interesting...

I am starting a line of sexual performance enhancement products. This will be the first of several products basically. Keep in mind, I am the type of business person to stay with one company for years if they provide me with quality work.

This particular product is a male sexual performance pill. The name of the product is "Velmora Crest." The packaging of the pills are a black bottle with a white top. Label on the product example would be perfect but at a minimum I have attached a "template" for your guidance.

Some of the technical aspects of this are as follows:

-File Format: Illustrator CS6 is preferred. (Winner must provide artwork in layer and can not flatten artwork.)
-Resolution: 300 dpi minimum
-Bleed: 1/16th (0.0625") inch from edge of label
-Color Mode: CMYK only or must be converted to CMYK for final production

Lastly, this is your project as a designer, artist, creator, this is essentially a piece of you that will be sold and known by thousands of people. I have no color scheme that I prefer, just use the template and follow the layout. If you have any further questions, please feel free to contact me at any time.
Updates

Quick note on the product and what it does: -Powerful, long lasting, harder erections -Works in a minutes and last for hours -Enhances sexual desire and drive Thank you for your ideas...

Project Deadline Extended
Reason: We decided to extent the project for a few more days to let the last few concepts come in. So far things are looking really good and we definitely have seen some amazing designs. Thank you for your hard work and amazing creativity. Looking forward to seeing what we have come in the next couple of day. Very respectfully, Brev

ONLY THREE DAYS LEFT!!!! Please submit your ideas as soon as possible. And as always, thank you for your help!!! V/r, Brev

Industry/Entity Type

Graphic Design

```html
<!DOCTYPE html>
<html lang="en">
<head>
<meta charset="utf-8">
<title>Velmora Crest – Label</title>
<link rel="stylesheet" href="https://fonts.googleapis.com/css2?family=Open+Sans:ital,wght@0,400;0,600;1,600&family=Roboto+Condensed:wght@700&display=swap">
<style>
  :root {
    --backdrop-light: #f4f4f4;
    --backdrop-dark: #d8d8d8;
    --label-black: #0a0a0b;
    --silver-light: #f0f0f1;
    --silver-mid: #a4a5a7;
    --silver-dark: #55565a;
    --neon-blue: #1fb6ff;
    --neon-yellow: #e2f01c;
    --photo-light: #9a9a9a;
    --photo-mid: #555555;
    --photo-dark: #1a1a1a;
    --text-white: #ffffff;
    --text-mint: #d7f4ec;
    --text-grey: #d4d5d7;
  }
  * { margin: 0; padding: 0; box-sizing: border-box; }
  html, body { width: 1200px; height: 960px; overflow: hidden; }
  body {
    background: radial-gradient(ellipse at center, var(--backdrop-light) 0%, var(--backdrop-dark) 100%);
    font-family: "Open Sans", Arial, sans-serif;
    position: relative;
  }
  .label {
    position: absolute;
    left: 290px;
    top: 115px;
    width: 620px;
    height: 733px;
    background: var(--label-black);
    overflow: hidden;
  }
  .label__band {
    position: absolute;
    left: 0;
    width: 100%;
    height: 20px;
    background: linear-gradient(180deg, var(--silver-dark) 0%, var(--silver-light) 45%, var(--silver-mid) 100%);
    z-index: 6;
  }
  .label__band--top { top: 0; }
  .label__band--bottom { bottom: 0; }

  .label__photo {
    position: absolute;
    left: 193px;
    top: 20px;
    width: 427px;
    height: 693px;
    background:
      radial-gradient(ellipse 55% 35% at 48% 52%, var(--photo-light) 0%, var(--photo-mid) 55%, transparent 100%),
      radial-gradient(ellipse 40% 22% at 70% 20%, #7a7a7a 0%, transparent 100%),
      linear-gradient(180deg, var(--photo-dark) 0%, #2b2b2b 50%, var(--photo-dark) 100%);
    -webkit-mask-image: linear-gradient(90deg, transparent 0%, #000 28%);
            mask-image: linear-gradient(90deg, transparent 0%, #000 28%);
    z-index: 1;
  }
  .label__pattern {
    position: absolute;
    z-index: 2;
  }
  .label__pattern--blue {
    left: 0;
    top: 220px;
    width: 380px;
    height: 513px;
    background: radial-gradient(ellipse 70% 60% at 35% 50%, rgba(31,182,255,0.55) 0%, rgba(31,182,255,0.22) 45%, transparent 80%);
    mix-blend-mode: screen;
  }
  .label__pattern--yellow {
    left: 273px;
    top: 20px;
    width: 347px;
    height: 480px;
    background: radial-gradient(ellipse 65% 60% at 55% 45%, rgba(226,240,28,0.5) 0%, rgba(226,240,28,0.2) 45%, transparent 80%);
    mix-blend-mode: screen;
  }

  .tagline {
    position: absolute;
    left: 40px;
    top: 72px;
    width: 340px;
    text-align: right;
    color: var(--text-white);
    font-style: italic;
    font-weight: 600;
    font-size: 26px;
    line-height: 1.33;
    letter-spacing: 1.6px;
    text-transform: uppercase;
    z-index: 4;
  }
  .brand {
    position: absolute;
    left: 110px;
    top: 438px;
    width: 432px;
    display: flex;
    align-items: center;
    justify-content: center;
    gap: 12px;
    z-index: 4;
  }
  .brand__mark {
    width: 22px;
    height: 22px;
    border-radius: 50%;
    background: var(--text-grey);
    flex: none;
  }
  .brand__name {
    color: var(--text-grey);
    font-weight: 400;
    font-size: 54px;
    line-height: 1;
    letter-spacing: -1px;
    white-space: nowrap;
  }
  .claim {
    position: absolute;
    left: 110px;
    top: 512px;
    width: 432px;
    text-align: center;
    color: var(--text-mint);
    font-family: "Roboto Condensed", "Arial Narrow", sans-serif;
    font-weight: 700;
    font-size: 30px;
    letter-spacing: 1.5px;
    z-index: 4;
  }
  .contents {
    position: absolute;
    left: 352px;
    top: 660px;
    color: var(--text-white);
    z-index: 4;
  }
  .contents__type {
    font-size: 18px;
    line-height: 1.1;
    color: var(--text-grey);
  }
  .contents__count {
    font-size: 32px;
    line-height: 1.1;
    letter-spacing: 0.5px;
  }
</style>
</head>
<body>
  <main class="label">
    <div class="label__band label__band--top"></div>

    <div class="label__photo" role="img" aria-label="Black and white photo of a shirtless muscular man, head bowed"></div>
    <div class="label__pattern label__pattern--blue" role="img" aria-label="Glowing blue neon line pattern"></div>
    <div class="label__pattern label__pattern--yellow" role="img" aria-label="Glowing yellow neon line pattern"></div>

    <p class="tagline">Reach your peak<br>performance<br>pure and potent</p>

    <div class="brand">
      <span class="brand__mark"></span>
      <span class="brand__name">Velmora Crest</span>
    </div>
    <p class="claim">Enhances sexual desire</p>

    <div class="contents">
      <p class="contents__type">Dietary Supplement</p>
      <p class="contents__count">60 Capsules</p>
    </div>

    <div class="label__band label__band--bottom"></div>
  </main>
</body>
</html>
```